Power Point Template Vierklang sustainability consulting

(find english description below)
We are a small German start-up that offers sustainability consulting. For presentations of results, our company presentation, proposals, lectures, etc., we need a PowerPoint template that matches our logo. We come from classic management consulting / strategy consulting and also deal with facts and figures in sustainability consulting. Therefore, the template should not be too fancy and should not only consist of photos. But it shouldn't be a completely sober template either. Our logo with the green leaves for sustainability (three leaves for VIERklang) and the white bar chart (with the dynamic swing upwards) reflects our attitude well, where we see ourselves on the range from playful to sober and classic to modern.

It might be nice for the template to include the shape of one of the leaves (from the logo). Also, the logo should appear in a corner of each slide. The colors from the logo (see appendix) should be partially reflected in the presentation. We can also imagine a gold-brown tone (see website www.vierklang-beratung.de) or a coral tone as a contrast. (Attention - the website is not final yet).

For a first suggestion, it is sufficient to suggest three to four slides (cover sheet, chapter/separation slide, text slide, data slide). We will then mark drafts that we like. In total, we would then need about 6-10 more slide templates, e.g. about us, team, slide for a statement, 2-3 data charts (pie, bar, column), top 3 - 5 list, timeline, contact (more slides are welcome ).

We are a small German start-up offering sustainability consulting. We need a power point template for result presentations, our company presentation, proposals, lectures etc. The template should be aligned with our logo. Our background lies in classic management consulting / strategy consulting and we also deal with facts and figures in sustainability consulting. Therefore, the template should not be too playful and not only consist of photos. But it should also not be a completely clear template. Our logo with the green leaves for sustainability (three leaves for VIERklang) and the white bar chart (with the dynamic upward swing) reflects our attitude well, where we see ourselves on the range from playful to down-to-earth and classic to modern .

For the template, it might be nice to incorporate the shape of one of the leaves (from the logo). Also, the logo should show up in one corner on each slide. Some of the colors from the logo (see attachment) should be reflected in the presentation. We could also think of a gold-brown tone (see website www.vierklang-beratung.de) or a coral tone for contrast. (Attention - the website is not final yet).

For a first proposal it is quite sufficient to suggest us three to four slides (cover page, chapter/separation slide, text slide, data slide). We will then mark the drafts that we like. In total we would need about 6-10 more slide templates, eg About us, Team, slide for a statement, 2-3 data charts (pie, bar, column), Top 3 - 5 List, Timeline, Contact (more slides are welcome).

Target Market(s)

Corporations, large companies and SMEs

Industry/Entity Type

Unternehmensberatung, Nachhaltigkeitsberatung

Font styles to use
Sans Serif
Other font styles liked:
• Calibri

Colors
00AB8E
00BBA5
67D7C9
C6EFE9
E9F9F6

Requirements
Must have
• see description (e.g. the colors of our logo)
Nice to have
• see description (e.g. elements of the logo included)
Should not have
• see description

```html
<!DOCTYPE html>
<html lang="en">
<head>
<meta charset="utf-8">
<title>Vierklang Sustainability Consulting – Slide Template</title>
<link rel="stylesheet" href="https://fonts.googleapis.com/css2?family=Carlito:wght@400;700&display=swap">
<style>
:root{
  --sand:#e8e0c6;
  --sand-line:#cdc3a4;
  --teal-900:#00AB8E;
  --teal-700:#00BBA5;
  --teal-500:#67D7C9;
  --teal-200:#C6EFE9;
  --teal-100:#E9F9F6;
  --leaf:#6e9e2c;
  --lime:#9cc83c;
  --lime-soft:#c9e06a;
  --ink:#2b2b2b;
  --ink-soft:#4a4a4a;
  --logo-grey:#5a5a5a;
}
*{box-sizing:border-box;margin:0;padding:0}
html,body{width:1200px;height:4124px;overflow:hidden;background:#fff}
body{position:relative;font-family:"Carlito","Calibri",sans-serif;color:var(--ink)}
.slide{position:absolute;left:51px;width:1096px;height:616px;background:var(--sand);overflow:hidden}
.slide--cover{top:58px}
.slide--about{top:738px}
.slide--team{top:1418px}
.slide--data{top:2098px}
.slide--timeline{top:2776px}
.slide--contact{top:3456px}
.abs{position:absolute}

/* brand mark */
.brand{position:absolute;display:flex;align-items:center;gap:10px}
.brand__dot{width:32px;height:32px;border-radius:50%;background:var(--lime)}
.brand__name{font-size:36px;font-weight:400;color:var(--logo-grey);letter-spacing:.5px;line-height:1}
.brand--footer{left:19px;top:548px}
.brand--cover{left:19px;top:20px}

.footer-rule{position:absolute;left:250px;top:578px;width:780px;height:1px;background:var(--sand-line)}
.page-num{position:absolute;width:28px;height:28px;border-radius:50%;background:var(--teal-900);color:#fff;font-size:12px;display:flex;align-items:center;justify-content:center}
.page-num--footer{left:1045px;top:564px}

.slide-title{position:absolute;left:0;width:100%;text-align:center;font-size:52px;font-weight:400;color:var(--ink);line-height:1}

/* cover */
.cover-art{position:absolute;left:0;top:0}
.cover-title{position:absolute;left:0;top:430px;width:100%;text-align:center;color:#fff;font-size:41px;line-height:1.25;letter-spacing:.3px}

/* about */
.about-title{position:absolute;left:645px;top:70px;font-size:54px;font-weight:400}
.about-lead{position:absolute;left:645px;top:150px;width:400px;font-size:21px;line-height:1.4;color:var(--ink-soft)}
.feature{position:absolute;left:648px;display:flex;align-items:center;gap:16px;font-size:21px;color:var(--ink-soft)}
.feature__icon{width:58px;height:58px;border-radius:50%;background:var(--teal-900);display:flex;align-items:center;justify-content:center;box-shadow:0 0 0 3px rgba(0,171,142,.18)}
.feature__icon--light{background:var(--teal-500)}

/* team */
.member{position:absolute;top:160px;width:280px;text-align:center}
.member__name{position:absolute;top:272px;left:0;width:100%;font-size:21px;font-weight:700;color:var(--ink)}
.member__role{position:absolute;top:306px;left:0;width:100%;font-size:15px;color:var(--ink-soft)}

/* data */
.chart-label{position:absolute;left:474px;font-size:15px;color:var(--ink);line-height:1}
.data-copy{position:absolute;left:597px;width:432px;font-size:21px;line-height:1.37;text-align:justify;color:var(--ink-soft)}

/* timeline */
.step-label{position:absolute;width:200px;text-align:center;font-size:15px;font-weight:700;color:var(--ink)}

/* contact */
.thanks-title{position:absolute;left:70px;top:92px;font-size:54px;font-weight:400}
.thanks-copy{position:absolute;left:73px;top:163px;width:360px;font-size:13px;line-height:1.75;color:var(--ink-soft)}
.contact-row{position:absolute;left:73px;display:flex;gap:14px;align-items:flex-start}
.contact-row__icon{width:42px;height:42px;border-radius:50%;background:var(--teal-900);display:flex;align-items:center;justify-content:center;flex:none;margin-top:2px}
.contact-row__label{font-size:16px;color:var(--ink);margin-bottom:6px}
.contact-row__value{font-size:11px;color:var(--ink-soft);line-height:1.9}
</style>
</head>
<body>

<!-- 01 Cover -->
<section class="slide slide--cover">
  <svg class="cover-art" width="1096" height="616" viewBox="0 0 1096 616">
    <defs>
      <linearGradient id="coverPhoto" x1="0" y1="0" x2="1" y2="1">
        <stop offset="0" stop-color="#8d8d86"/>
        <stop offset=".45" stop-color="#5d5a54"/>
        <stop offset="1" stop-color="#2c2a27"/>
      </linearGradient>
    </defs>
    <path role="img" aria-label="Photo: consultant presenting at a flip chart to a seated team" fill="url(#coverPhoto)"
      d="M0,118 C40,40 110,0 190,0 L1005,0 C1060,40 1090,90 1096,110 C1000,330 820,540 560,616 L0,616 Z"/>
    <path fill="var(--lime)" d="M1096,150 C1040,360 880,540 640,616 L1096,616 Z"/>
    <path fill="var(--lime-soft)" d="M1096,330 C1030,470 900,570 780,616 L1096,616 Z"/>
    <path fill="none" stroke="var(--sand)" stroke-width="10" d="M1096,110 C1000,330 820,540 560,616"/>
  </svg>
  <div class="brand brand--cover"><span class="brand__dot"></span><span class="brand__name">Vierklang</span></div>
  <h1 class="cover-title">VIERKLANG SUSTAINABILITY<br>CONSULTING</h1>
  <div class="page-num" style="left:1056px;top:580px">01</div>
</section>

<!-- 02 About us -->
<section class="slide slide--about">
  <svg class="abs" style="left:37px;top:50px" width="560" height="475" viewBox="0 0 560 475">
    <defs>
      <linearGradient id="aboutPhoto" x1="0" y1="0" x2="1" y2="1">
        <stop offset="0" stop-color="#b9b6ac"/>
        <stop offset=".5" stop-color="#6f6a62"/>
        <stop offset="1" stop-color="#3a3835"/>
      </linearGradient>
    </defs>
    <path role="img" aria-label="Photo: colleagues reviewing documents at a meeting table" fill="url(#aboutPhoto)"
      d="M0,365 C70,160 250,20 430,0 C400,120 420,230 552,340 C420,460 270,490 140,450 C70,430 20,400 0,365 Z"/>
    <path fill="none" stroke="var(--sand)" stroke-width="5" d="M20,380 C160,190 330,130 552,340"/>
  </svg>
  <h2 class="about-title">About Us</h2>
  <p class="about-lead">Nice that you are here.<br>With our experience, our expertise and our passion, we accompany you on your sustainable path to future viability.</p>
  <div class="feature" style="top:290px">
    <span class="feature__icon"><svg width="30" height="30" viewBox="0 0 30 30" fill="none" stroke="#fff" stroke-width="1.8"><circle cx="15" cy="15" r="5"/><circle cx="15" cy="15" r="10" stroke-dasharray="4 3"/></svg></span>Our way of working</div>
  <div class="feature" style="top:379px">
    <span class="feature__icon"><svg width="30" height="30" viewBox="0 0 30 30" fill="none" stroke="#fff" stroke-width="1.8"><circle cx="15" cy="9" r="4"/><path d="M7,25 C7,18 23,18 23,25"/></svg></span>Our experience</div>
  <div class="feature" style="top:467px">
    <span class="feature__icon feature__icon--light"><svg width="30" height="30" viewBox="0 0 30 30" fill="none" stroke="#fff" stroke-width="1.8"><circle cx="15" cy="16" r="9"/><path d="M6,16 H24 M15,7 C11,12 11,20 15,25 C19,20 19,12 15,7"/></svg></span>Our background on sustainability</div>
  <div class="brand brand--footer"><span class="brand__dot"></span><span class="brand__name">Vierklang</span></div>
  <div class="footer-rule"></div>
  <div class="page-num page-num--footer">02</div>
</section>

<!-- 03 Team -->
<section class="slide slide--team">
  <h2 class="slide-title" style="top:70px">Our Team</h2>

  <div class="member" style="left:137px">
    <svg width="280" height="260" viewBox="0 0 280 260">
      <path fill="none" stroke="var(--leaf)" stroke-width="3" d="M232,120 A112,112 0 1 1 160,24"/>
      <circle cx="232" cy="120" r="5" fill="var(--lime)"/>
      <circle role="img" aria-label="Portrait photo of Dr Mara Lindholt" cx="140" cy="134" r="93" fill="#b4aca0"/>
    </svg>
    <div class="member__name">Dr Mara Lindholt</div>
    <div class="member__role">Managing Partners</div>
  </div>

  <div class="member" style="left:404px">
    <svg width="280" height="260" viewBox="0 0 280 260">
      <path fill="none" stroke="var(--leaf)" stroke-width="3" d="M232,120 A112,112 0 1 1 160,24"/>
      <circle cx="232" cy="120" r="5" fill="var(--lime)"/>
      <circle role="img" aria-label="Portrait photo of Dr Jana Falk" cx="140" cy="134" r="93" fill="#bdb6aa"/>
    </svg>
    <div class="member__name">Dr Jana Falk</div>
    <div class="member__role">Managing Partners</div>
  </div>

  <div class="member" style="left:671px">
    <svg width="280" height="260" viewBox="0 0 280 260">
      <path fill="none" stroke="var(--leaf)" stroke-width="3" d="M232,120 A112,112 0 1 1 160,24"/>
      <circle cx="232" cy="120" r="5" fill="var(--lime)"/>
      <circle role="img" aria-label="Portrait photo of Dr Paula Brenner-Ost" cx="140" cy="134" r="93" fill="#aaa296"/>
    </svg>
    <div class="member__name">Dr Paula Brenner-Ost</div>
    <div class="member__role">Managing Partners</div>
  </div>

  <div class="brand brand--footer"><span class="brand__dot"></span><span class="brand__name">Vierklang</span></div>
  <div class="footer-rule"></div>
  <div class="page-num page-num--footer">03</div>
</section>

<!-- 04 Data chart -->
<section class="slide slide--data">
  <h2 class="slide-title" style="top:70px">Data Charts</h2>
  <svg class="abs" style="left:0;top:0" width="600" height="560" viewBox="0 0 600 560">
    <rect x="66" y="158" width="82" height="344" fill="var(--teal-900)"/>
    <rect x="66" y="158" width="10" height="344" fill="#008f77"/>
    <rect x="134" y="222" width="74" height="280" fill="var(--teal-700)"/>
    <rect x="194" y="275" width="80" height="227" fill="var(--teal-500)"/>
    <rect x="256" y="331" width="78" height="171" fill="var(--teal-200)"/>
    <rect x="320" y="378" width="78" height="124" fill="var(--teal-100)"/>
    <g stroke="var(--teal-900)" stroke-width="1.2" fill="var(--teal-900)">
      <line x1="190" y1="181" x2="464" y2="181"/><circle cx="190" cy="181" r="5"/>
      <line x1="250" y1="238" x2="464" y2="238"/><circle cx="250" cy="238" r="5"/>
      <line x1="306" y1="296" x2="464" y2="296"/><circle cx="306" cy="296" r="5"/>
      <line x1="363" y1="352" x2="464" y2="352"/><circle cx="363" cy="352" r="5"/>
      <line x1="421" y1="410" x2="464" y2="410"/><circle cx="421" cy="410" r="5"/>
    </g>
  </svg>
  <span class="chart-label" style="top:174px">1000</span>
  <span class="chart-label" style="top:231px">1000</span>
  <span class="chart-label" style="top:289px">1000</span>
  <span class="chart-label" style="top:345px">1000</span>
  <span class="chart-label" style="top:403px">1000</span>
  <p class="data-copy" style="top:170px">Lorem ipsum dolorsitamet, consectetur adipiscing elit, sed do eiusmod tempor incididunt ut labore et dolore magna aliqua. Ut enim ad minim veniam, quis nostrud exercitation ullamco laboris nisi ut aliquip ex ea commodo consequat. Duis aute irure dolor in reprehenderit in voluptate velit esse cillum dolore eu fugiat nulla pariatur.</p>
  <p class="data-copy" style="top:428px">Excepteur sint occaecat cupidatat non proident, sunt in culpa qui officia deserunt mollit anim id est laborum.</p>
  <div class="brand brand--footer"><span class="brand__dot"></span><span class="brand__name">Vierklang</span></div>
  <div class="footer-rule"></div>
  <div class="page-num page-num--footer">04</div>
</section>

<!-- 05 Timeline -->
<section class="slide slide--timeline">
  <h2 class="slide-title" style="top:70px">Timeline</h2>
  <svg class="abs" style="left:0;top:0" width="1096" height="520" viewBox="0 0 1096 520">
    <g fill="none" stroke="var(--teal-900)" stroke-width="1.5">
      <polyline points="144,278 341,344 538,278 733,344 930,278"/>
      <g stroke-dasharray="2 4" stroke-width="2">
        <line x1="144" y1="355" x2="144" y2="413"/>
        <line x1="538" y1="355" x2="538" y2="413"/>
        <line x1="930" y1="355" x2="930" y2="413"/>
        <line x1="341" y1="218" x2="341" y2="267"/>
        <line x1="733" y1="218" x2="733" y2="267"/>
      </g>
    </g>
    <g fill="var(--sand)" stroke="var(--teal-900)" stroke-width="2" stroke-dasharray="2 4">
      <circle cx="144" cy="278" r="77"/><circle cx="341" cy="344" r="77"/>
      <circle cx="538" cy="278" r="77"/><circle cx="733" cy="344" r="77"/>
      <circle cx="930" cy="278" r="77"/>
    </g>
    <g fill="#fff" stroke="var(--teal-900)" stroke-width="3">
      <circle cx="144" cy="278" r="58"/><circle cx="341" cy="344" r="58"/>
      <circle cx="538" cy="278" r="58"/><circle cx="733" cy="344" r="58"/>
      <circle cx="930" cy="278" r="58"/>
    </g>
    <g fill="var(--sand)" stroke="var(--teal-900)" stroke-width="1.5">
      <circle cx="212" cy="301" r="5"/><circle cx="273" cy="321" r="5"/>
      <circle cx="409" cy="321" r="5"/><circle cx="470" cy="301" r="5"/>
      <circle cx="606" cy="301" r="5"/><circle cx="665" cy="321" r="5"/>
      <circle cx="801" cy="321" r="5"/><circle cx="862" cy="301" r="5"/>
    </g>
    <g fill="var(--teal-900)">
      <circle cx="144" cy="421" r="9"/><circle cx="538" cy="421" r="9"/><circle cx="930" cy="421" r="9"/>
      <circle cx="341" cy="210" r="9"/><circle cx="733" cy="210" r="9"/>
    </g>
    <g fill="#fff" font-size="8" text-anchor="middle" font-family="Carlito, sans-serif">
      <text x="144" y="424">01</text><text x="341" y="213">02</text><text x="538" y="424">03</text>
      <text x="733" y="213">04</text><text x="930" y="424">05</text>
    </g>
    <g fill="none" stroke="var(--teal-900)" stroke-width="2.2" stroke-linecap="round">
      <!-- globe -->
      <circle cx="144" cy="280" r="22"/><path d="M122,280 H166 M144,258 C134,268 134,292 144,302 C154,292 154,268 144,258"/>
      <!-- bulb -->
      <path d="M331,360 C320,350 320,330 341,326 C362,330 362,350 351,360 Z M333,366 H349 M335,372 H347"/>
      <path d="M341,314 V308 M322,322 L317,318 M360,322 L365,318"/>
      <!-- report -->
      <rect x="524" y="256" width="28" height="40" rx="2"/><path d="M530,266 H546 M530,274 H546 M530,282 H540"/><circle cx="556" cy="296" r="7"/>
      <!-- desk -->
      <circle cx="733" cy="326" r="6"/><path d="M721,348 C721,336 745,336 745,348 M712,352 H754 M718,352 V368 M748,352 V368"/>
      <!-- team -->
      <circle cx="916" cy="266" r="5"/><circle cx="930" cy="262" r="5"/><circle cx="944" cy="266" r="5"/>
      <path d="M908,288 C908,276 924,276 924,288 M922,286 C922,272 938,272 938,286 M936,288 C936,276 952,276 952,288 M906,296 H954"/>
    </g>
  </svg>
  <div class="step-label" style="left:44px;top:450px">Duis aute irure</div>
  <div class="step-label" style="left:241px;top:163px">Duis aute irure</div>
  <div class="step-label" style="left:438px;top:450px">Duis aute irure</div>
  <div class="step-label" style="left:633px;top:163px">Duis aute irure</div>
  <div class="step-label" style="left:830px;top:450px">Duis aute irure</div>
  <div class="brand brand--footer"><span class="brand__dot"></span><span class="brand__name">Vierklang</span></div>
  <div class="footer-rule"></div>
  <div class="page-num page-num--footer">05</div>
</section>

<!-- 06 Contact -->
<section class="slide slide--contact">
  <h2 class="thanks-title">Thank You</h2>
  <p class="thanks-copy">Lorem ipsum dolor sit amet, consectetur adipiscing elit, sed do eiusmod tempor incididunt ut labore et dolore magna quis nostrud exercitation ullamco laboris nisi ut aliquip ex ea commodo consequat.</p>

  <div class="contact-row" style="top:265px">
    <span class="contact-row__icon"><svg width="18" height="18" viewBox="0 0 18 18"><path fill="#fff" d="M9,1 C5.5,1 3,3.5 3,7 C3,11 9,17 9,17 C9,17 15,11 15,7 C15,3.5 12.5,1 9,1 Z"/><circle cx="9" cy="7" r="2.3" fill="var(--teal-900)"/></svg></span>
    <div><div class="contact-row__label">Address :</div><div class="contact-row__value">Lumen Office Park Talweg 14<br>63110 Rodgau / Frankfurt a. M</div></div>
  </div>
  <div class="contact-row" style="top:352px">
    <span class="contact-row__icon"><svg width="18" height="18" viewBox="0 0 18 18"><path fill="#fff" d="M4,1.5 L7,1.5 L8,5.5 L6,7 C7,9.5 8.5,11 11,12 L12.5,10 L16.5,11 L16.5,14 C16.5,15.5 15,16.5 13.5,16.3 C7,15.5 2.5,11 1.7,4.5 C1.5,3 2.5,1.5 4,1.5 Z"/></svg></span>
    <div><div class="contact-row__label">Phone :</div><div class="contact-row__value">+49 (0) 6106 – 482 3907</div></div>
  </div>
  <div class="contact-row" style="top:437px">
    <span class="contact-row__icon"><svg width="18" height="18" viewBox="0 0 18 18"><rect x="1.5" y="4" width="15" height="10" rx="1.2" fill="#fff"/><path d="M2,4.5 L9,10 L16,4.5" fill="none" stroke="var(--teal-900)" stroke-width="1.4"/></svg></span>
    <div><div class="contact-row__label">Email Address :</div><div class="contact-row__value">info@vierklang-beratung.de</div></div>
  </div>

  <svg class="abs" style="left:470px;top:64px" width="490" height="470" viewBox="0 0 490 470">
    <defs>
      <linearGradient id="contactPhoto" x1="0" y1="0" x2="1" y2="1">
        <stop offset="0" stop-color="#c3c0b8"/>
        <stop offset=".5" stop-color="#7a746b"/>
        <stop offset="1" stop-color="#34343a"/>
      </linearGradient>
    </defs>
    <path role="img" aria-label="Photo: two colleagues working together at a desk with a laptop" fill="url(#contactPhoto)"
      d="M0,155 C110,70 250,40 372,0 C330,80 300,150 400,260 C455,320 480,380 470,450 C330,470 190,465 90,420 C30,380 0,300 0,155 Z"/>
    <path fill="none" stroke="var(--sand)" stroke-width="5" d="M40,400 C150,240 300,180 470,260"/>
  </svg>

  <div class="brand brand--footer"><span class="brand__dot"></span><span class="brand__name">Vierklang</span></div>
  <div class="page-num page-num--footer">06</div>
</section>

</body>
</html>
```